Landscape design build company door flyer

I would like this flyer to convey a high-level of professionalism for a company that is excellent with communication with their clients as well as a company that does incredible installations

Went on vacation/holiday

```html
<!DOCTYPE html>
<html lang="en">
<head>
<meta charset="utf-8">
<title>Cedarline Builders – Outdoor Living Flyer</title>
<link rel="stylesheet" href="https://fonts.googleapis.com/css2?family=Montserrat:wght@400;500;600;700;800&display=swap">
<style>
  :root{
    --navy:#0f2a40;
    --navy-deep:#0b2336;
    --gold:#f5b301;
    --white:#ffffff;
    --paper-grey:#f1f1f1;
    --stage:#e6e6e6;
  }
  *{margin:0;padding:0;box-sizing:border-box}
  html,body{width:1200px;height:1029px;overflow:hidden}
  body{background:var(--stage);font-family:"Montserrat",sans-serif;position:relative}

  .flyer{position:absolute;left:211px;top:14px;width:778px;height:1000px;background:var(--white);overflow:hidden;box-shadow:0 6px 24px rgba(0,0,0,.18)}
  .hero{position:absolute;left:0;top:49px;width:778px;height:654px;background:var(--navy)}
  .top-shape{position:absolute;left:0;top:0;width:778px;height:172px}
  .brand{position:absolute;left:291px;top:0;width:187px;height:136px;display:flex;flex-direction:column;align-items:center;justify-content:center;gap:7px;color:var(--navy);background:var(--white)}
  .brand-mark{width:26px;height:26px;border-radius:50%;background:var(--navy)}
  .brand-name{font-weight:700;font-size:14px;letter-spacing:.3px;text-align:center;line-height:1.15}
  .brand-tag{display:block;font-size:8px;font-weight:700;letter-spacing:.2px}

  .headline{position:absolute;left:0;top:122px;width:778px;text-align:center;font-weight:800;font-size:44px;line-height:47px;color:var(--white);letter-spacing:.2px}
  .headline .accent{color:var(--gold)}

  .about{position:absolute;left:61px;top:300px;width:269px;color:var(--white)}
  .about h2{font-size:18px;font-weight:600;line-height:22px;margin-bottom:8px}
  .about p{font-size:11.9px;line-height:14.9px;text-align:justify;hyphens:auto;-webkit-hyphens:auto;margin-bottom:14.9px}
  .about p:last-child{margin-bottom:0}

  .photo{position:absolute}
  .photo-deck{left:369px;top:307px;width:130px;height:129px;background:linear-gradient(160deg,#3f6b2e,#7b4a2c 60%,#5a2e1a)}
  .photo-pavilion{left:510px;top:307px;width:208px;height:129px;background:linear-gradient(180deg,#8a5a38,#5c5a55 45%,#3f4650)}
  .photo-pool{left:369px;top:447px;width:130px;height:91px;background:linear-gradient(180deg,#d9dcd6,#7fc6bd 60%,#3f8f8a)}
  .photo-steps{left:369px;top:547px;width:130px;height:91px;background:linear-gradient(180deg,#6a6248,#5e6066 45%,#3e4046)}
  .photo-firepit{left:510px;top:447px;width:208px;height:191px;background:linear-gradient(180deg,#3d66a8,#2a4672 40%,#3a3630 70%,#6b5a4a)}

  .services{position:absolute;left:0;top:703px;width:778px;height:173px;background:var(--white)}
  .services h2{position:absolute;left:61px;top:10px;font-size:18px;line-height:24px;font-weight:700;color:var(--navy)}
  .service{position:absolute;display:flex;align-items:center;gap:9px;font-size:11.5px;font-weight:700;color:var(--navy);letter-spacing:.2px}
  .service svg{width:27px;height:27px;flex:none}
  .seal{position:absolute;left:600px;top:34px;width:118px;height:118px}

  .contact{position:absolute;left:0;top:876px;width:778px;height:118px;background:var(--navy-deep)}
  .contact h2{position:absolute;left:61px;top:15px;font-size:15.5px;line-height:20px;font-weight:600;color:var(--white)}
  .phone{position:absolute;left:59px;top:38px;display:flex;align-items:center;gap:14px;color:var(--gold);font-weight:600;font-size:40px;line-height:48px;letter-spacing:.5px}
  .phone svg{width:38px;height:38px}
  .email{position:absolute;right:31px;top:50px;font-size:15px;line-height:20px;color:var(--white);letter-spacing:.3px}
</style>
</head>
<body>
<main class="flyer">
  <section class="hero">
    <h1 class="headline">LET’S CREATE<br><span class="accent">YOUR DREAM OUTDOOR</span><br>LIVING SPACE!</h1>

    <article class="about">
      <h2>ABOUT US</h2>
      <p>Discover the endless possibilities for your outdoor space with The Cedarline Builders Team. Our team of skilled artisans is dedicated to turning your outdoor space into a breathtaking oasis that you’ll love coming home to. Whether it’s a cozy patio for intimate gatherings, a sprawling deck to host memorable parties, or a custom paver driveway that adds instant curb appeal, our high-quality craftsmanship ensures stunning results that exceed your expectations.</p>
      <p>From concept to completion, we take pride in every detail, using the finest materials to withstand Seattle’s climate while adding timeless elegance to your property. Embrace the Pacific Northwest lifestyle and create cherished moments with family and friends in a captivating outdoor haven.</p>
    </article>

    <div class="photo photo-deck" role="img" aria-label="Photo of a wooden deck with pergola and patio chairs"></div>
    <div class="photo photo-pavilion" role="img" aria-label="Photo of a covered outdoor pavilion with stone fireplace"></div>
    <div class="photo photo-pool" role="img" aria-label="Photo of a backyard pool beside a modern house"></div>
    <div class="photo photo-steps" role="img" aria-label="Photo of stone retaining wall with steps"></div>
    <div class="photo photo-firepit" role="img" aria-label="Photo of a paver patio with fire pit overlooking a lake at dusk"></div>
  </section>

  <svg class="top-shape" viewBox="0 0 778 172" aria-hidden="true">
    <rect x="0" y="0" width="778" height="49" fill="#ffffff"/>
    <rect x="228" y="0" width="63" height="49" fill="#f1f1f1"/>
    <rect x="478" y="0" width="63" height="49" fill="#f1f1f1"/>
    <polygon points="228,49 541,49 478,136 291,136" fill="#f1f1f1"/>
    <line x1="291" y1="136" x2="291" y2="169" stroke="#0b1a26" stroke-width="1"/>
    <line x1="478" y1="136" x2="478" y2="169" stroke="#0b1a26" stroke-width="1"/>
  </svg>
  <div class="brand">
    <span class="brand-mark"></span>
    <div class="brand-name">CEDARLINE BUILDERS<span class="brand-tag">OUTDOOR LIVING SPACES</span></div>
  </div>

  <section class="services">
    <h2>OUR SERVICES</h2>
    <div class="service" style="left:62px;top:53px"><svg viewBox="0 0 27 27" aria-hidden="true"><path d="M3 11 13.5 3 24 11V25H3Z" fill="none" stroke="#0f2a40" stroke-width="1.8"/><path d="M8 14h11M13.5 12v9M9 21h9" stroke="#0f2a40" stroke-width="1.5"/></svg>Paver Patios</div>
    <div class="service" style="left:62px;top:92px"><svg viewBox="0 0 27 27" aria-hidden="true"><path d="M3 11 13.5 3 24 11V25H3Z" fill="none" stroke="#0f2a40" stroke-width="1.8"/><path d="M6 21 11 14h5l5 7Z" fill="#0f2a40"/></svg>Paver Driveways</div>
    <div class="service" style="left:62px;top:134px"><svg viewBox="0 0 27 27" aria-hidden="true"><path d="M3 11 13.5 3 24 11V25H3Z" fill="none" stroke="#0f2a40" stroke-width="1.8"/><path d="M8 13h8v3h-5v3h8" fill="none" stroke="#0f2a40" stroke-width="2"/></svg>Retaining Walls</div>
    <div class="service" style="left:228px;top:53px"><svg viewBox="0 0 27 27" aria-hidden="true"><path d="M3 11 13.5 3 24 11V25H3Z" fill="none" stroke="#0f2a40" stroke-width="1.8"/><path d="M10 11v8M17 11v8M10 14h7M7 20q2-1.5 4 0t4 0 4 0" fill="none" stroke="#0f2a40" stroke-width="1.5"/></svg>Pools</div>
    <div class="service" style="left:228px;top:92px"><svg viewBox="0 0 27 27" aria-hidden="true"><path d="M3 11 13.5 3 24 11V25H3Z" fill="none" stroke="#0f2a40" stroke-width="1.8"/><path d="M7 14h13M7 18h13M9 14v7M13.5 14v7M18 14v7" stroke="#0f2a40" stroke-width="1.5"/></svg>Decks &amp; Railings</div>
    <div class="service" style="left:228px;top:134px"><svg viewBox="0 0 27 27" aria-hidden="true"><path d="M3 11 13.5 3 24 11V25H3Z" fill="none" stroke="#0f2a40" stroke-width="1.8"/><path d="M8 22V15l5.5-4 5.5 4v7Z" fill="#0f2a40"/></svg>Firepits &amp; Fireplaces</div>
    <div class="service" style="left:399px;top:53px"><svg viewBox="0 0 27 27" aria-hidden="true"><path d="M3 11 13.5 3 24 11V25H3Z" fill="none" stroke="#0f2a40" stroke-width="1.8"/><rect x="11" y="12" width="5" height="7" rx="1" fill="none" stroke="#0f2a40" stroke-width="1.5"/><path d="M13.5 19v3" stroke="#0f2a40" stroke-width="1.5"/></svg>Outdoor Lighting</div>
    <div class="service" style="left:399px;top:92px"><svg viewBox="0 0 27 27" aria-hidden="true"><path d="M3 11 13.5 3 24 11V25H3Z" fill="none" stroke="#0f2a40" stroke-width="1.8"/><circle cx="13.5" cy="17" r="5" fill="none" stroke="#0f2a40" stroke-width="1.4"/><path d="M13.5 14v6M10.5 17h6" stroke="#0f2a40" stroke-width="1.4"/></svg>And More...</div>
    <svg class="seal" viewBox="0 0 118 118" role="img" aria-label="Experience seal">
      <circle cx="59" cy="59" r="58" fill="#c9a227"/>
      <circle cx="59" cy="59" r="46" fill="#2a2a2a"/>
      <circle cx="59" cy="59" r="40" fill="#d9b23a"/>
    </svg>
  </section>

  <section class="contact">
    <h2>CONTACT US TODAY</h2>
    <div class="phone">
      <svg viewBox="0 0 38 38" aria-hidden="true"><path d="M9 4 15 11 11 15q3 7 11 12l4-4 7 6-4 5Q17 34 5 15 4 9 9 4Z" fill="#f5b301"/><path d="M22 6a11 11 0 0 1 10 10M22 11a6 6 0 0 1 5 5" fill="none" stroke="#f5b301" stroke-width="2.4" stroke-linecap="round"/></svg>
      <span>[206]-555-0148</span>
    </div>
    <div class="email">info@cedarlinebuilders.com</div>
  </section>
</main>
</body>
</html>
```